SEO Friendly Web Design Needed for Leading Software Company

Founded in 1986, TRBW is the market leader for innovative software solutions for the heavy civil construction industry. Our suite of products, including the bestsellers GroundQuote® and SiteTrack®, are used by more than 40,000 workers every day to improve their proficiency at estimating, job management, resource management, safety and equipment maintenance. TRBW also offers new mobile applications and cloud computing services so companies can work on a wide array of devices including laptops, tablets and smartphones.

In addition to high quality software, TRBW is best known for providing world-class customer service, and for its friendly, employee-ownership culture. We offer a full range of professional support options to help customers maximize their software investment including implementation planning, training and INSTANT 24/7 phone support.

Goals, objectives and target audience

The goal of our new layout and design will be to increase conversions, enhance user experience and enhance our SERP rankings.

Our objectives are as follows:
1. Clean and well laid out home page. White space is OK.
2. CTAs in strategic locations throughout to drive conversions and MQLs
3. SEO rich content with appropriate layout to meet our SEO requirements
4. 2 Master Design Templates – Home & Internal
5. Custom Design elements for individual modules

Target Audience:
- Heavy / Civil Construction Industry
- C Level executives or persons in leadership roles who utilize our software
- MEN in the construction industry.

Requirements
Should not have
• Feminine design - our industry is largely male construction workers.
Don't use script or goofy fonts
Don't change the logo, or put it in an image where it is not easily viewable.

```html
<!DOCTYPE html>
<html lang="en">
<head>
<meta charset="utf-8">
<title>TRBW – Software Overview</title>
<link href="https://fonts.googleapis.com/css2?family=Open+Sans:wght@300;400;600;700&display=swap" rel="stylesheet">
<style>
:root{
  --orange:#f7941d;
  --green:#2bb04a;
  --ink:#2b2b2b;
  --text:#444;
  --muted:#8a8a8a;
  --line:#e2e2e2;
  --topbar:#3b3b3b;
  --btn-grey:#7b7b7b;
}
*{box-sizing:border-box;margin:0;padding:0}
html,body{width:1200px;height:2930px;overflow:hidden}
body{position:relative;background:#fff;font-family:'Open Sans',Arial,sans-serif;color:var(--text)}
.abs{position:absolute}

/* top bar */
.topbar{left:0;top:0;width:1200px;height:28px;background:var(--topbar);font-size:12px}
.topbar .quick{left:94px;top:6px;color:var(--orange)}
.topbar .quick span{color:#999;margin:0 4px}
.topbar .contact{right:94px;top:5px;color:var(--orange);display:flex;align-items:center;gap:8px}
.topbar .contact .phone{font-weight:700;font-size:15px;display:flex;align-items:center;gap:5px}

/* header */
.header{left:0;top:28px;width:1200px;height:102px;background:linear-gradient(#fff,#f4f4f4)}
.brand{left:94px;top:24px;display:flex;align-items:center;gap:12px}
.brand .square{width:14px;height:14px;background:var(--green)}
.brand .name{font-weight:700;font-size:38px;line-height:48px;color:var(--green);letter-spacing:1px}
.nav{right:94px;top:42px;display:flex;gap:30px;font-size:18px;color:#555}
.nav .active{color:var(--orange)}

/* hero */
.hero{left:0;top:130px;width:1200px;height:162px;background:linear-gradient(90deg,#3d3529,#6b5a3c 45%,#4a4236 70%,#2e2a24)}
.hero h1{left:94px;top:40px;font-size:42px;font-weight:700;color:#fff;letter-spacing:-1px;line-height:54px}
.hero p{left:96px;top:98px;font-size:17px;color:#fff}
.hero .devices{left:880px;top:20px;width:220px;height:126px;background:linear-gradient(#f2f2f2,#cfd4d8);border-radius:4px}

/* intro */
.intro h2{left:96px;top:362px;font-size:34px;font-weight:400;color:var(--ink);letter-spacing:-.5px}
.intro .lead{left:96px;top:418px;width:420px;font-size:17px;line-height:24px;color:#222}
.ticks{left:96px;top:486px;width:410px;list-style:none}
.ticks li{display:flex;align-items:center;gap:8px;height:37px;border-top:1px solid var(--line);font-size:13.5px;color:#222}
.ticks li:first-child{border-top:none}
.cta{top:652px;height:38px;color:#fff;font-weight:600;font-size:16px;display:flex;align-items:center;padding-left:18px;background:var(--green);white-space:nowrap;clip-path:polygon(0 0,92% 0,100% 50%,92% 100%,0 100%)}
.cta.sales{left:96px;width:170px}
.cta.demo{left:288px;width:150px}
.cta::after{content:"›";margin-left:10px;font-size:18px}

.thumbs{left:546px;top:372px;width:560px;display:grid;grid-template-columns:repeat(5,100px);column-gap:14px;row-gap:18px}
.thumb .pic{width:100px;height:100px;border:4px solid #fff;box-shadow:0 0 0 1px #ccc,0 2px 3px rgba(0,0,0,.2)}
.thumb p{font-size:12.5px;line-height:16px;color:#333;margin-top:6px}

.divider{left:530px;top:744px;width:140px;height:24px}

/* modules */
.module{width:470px;height:290px}
.module h3{font-size:26px;line-height:30px;font-weight:400;color:var(--orange);letter-spacing:-.5px;white-space:nowrap}
.module .photo{position:absolute;left:0;top:44px;width:230px;height:182px}
.module ul{position:absolute;left:250px;top:44px;width:196px;list-style:none}
.module li{height:30px;line-height:30px;border-bottom:1px solid var(--line);font-size:12.5px;font-weight:600;color:#333;white-space:nowrap}
.module li:last-child{border-bottom:none}
.module li::before{content:"+";color:var(--muted);margin:0 6px 0 2px}
.module .actions{position:absolute;left:250px;top:212px;display:flex;gap:8px}
.btn{height:24px;line-height:24px;font-size:11px;color:#fff;background:var(--btn-grey);padding:0 0 0 7px;white-space:nowrap;overflow:hidden;clip-path:polygon(0 0,88% 0,100% 50%,88% 100%,0 100%)}
.btn::after{content:" ›"}
.btn.sales{width:100px}.btn.more{width:90px}
.btn.green{background:var(--green)}.btn.orange{background:var(--orange)}

.to-top{left:1130px;top:1010px;width:70px;height:42px;background:#777;color:#fff;font-size:10px;line-height:11px;padding:9px 0 0 24px;font-weight:700}
.to-top svg{position:absolute;left:8px;top:10px}

/* footer */
.footer{left:0;top:2384px;width:1200px;height:494px;background:linear-gradient(#3a342a,#2a2620 40%,#2f2b22 75%,#3c3424)}
.footer .tab{left:566px;top:0;width:68px;height:44px;background:#fff;border-radius:0 0 4px 4px;display:flex;align-items:center;justify-content:center;font-weight:700;color:var(--green);font-size:17px}
.fcol{top:102px}
.fcol h4{color:var(--orange);font-size:17px;font-weight:600;padding-bottom:8px;border-bottom:1px solid #6b6459;width:154px;margin-bottom:10px}
.fcol ul{list-style:none}
.fcol li{font-size:12px;color:#eee;height:30px;line-height:26px;white-space:nowrap}
.fcol li::before{content:"+ ";color:#aaa}
.fcol li.current{background:#fff;color:var(--orange);width:154px;padding-left:4px}
.fcol h4.second{margin-top:14px}
.contact-list li::before{content:""}
.contact-list li{display:flex;align-items:flex-start;gap:8px;height:auto;min-height:30px;line-height:18px;padding-top:4px}
.contact-list .k{width:66px}
.social{display:flex;gap:8px;margin-top:4px}
.social span{width:30px;height:30px;border:2px solid #ddd;border-radius:50%}
.social span.on{border-color:#5aa8e0;background:#5aa8e0}
.follow{font-size:12px;color:#5aa8e0;margin-left:38px;margin-top:2px}

.bottombar{left:0;top:2878px;width:1200px;height:52px;background:var(--green);color:#fff;font-size:12.5px}
.bottombar .copy{left:94px;top:17px}
.bottombar .copy span{margin-left:20px}
</style>
</head>
<body>

<div class="abs topbar">
  <div class="abs quick">Tools <span>.</span> News <span>.</span> Blogs</div>
  <div class="abs contact">Contact Us <span style="color:#999">.</span> Sales <span style="color:#999">.</span>
    <span class="phone"><svg width="12" height="12" viewBox="0 0 24 24"><path fill="#f7941d" d="M6.6 10.8a15 15 0 0 0 6.6 6.6l2.2-2.2c.3-.3.7-.4 1-.2 1.1.4 2.3.6 3.6.6.6 0 1 .4 1 1V20c0 .6-.4 1-1 1A17 17 0 0 1 3 4c0-.6.4-1 1-1h3.5c.6 0 1 .4 1 1 0 1.2.2 2.4.6 3.6.1.3 0 .7-.2 1z"/></svg>1800 5550 1234</span></div>
</div>

<header class="abs header">
  <div class="abs brand">
    <span class="square"></span>
    <span class="name">TRBW</span>
  </div>
  <nav class="abs nav"><span class="active">Software</span><span>Services</span><span>Pricing</span><span>Careers</span><span>Events</span><span>About Us</span></nav>
</header>

<section class="abs hero" role="img" aria-label="Construction site with heavy machinery at dusk">
  <h1 class="abs">Software Overview</h1>
  <p class="abs">Trusted by Over 40,000 Construction Professionals</p>
  <div class="abs devices" role="img" aria-label="Software dashboard shown on desktop, tablet and phone"></div>
</section>

<section class="intro">
  <h2 class="abs">Construction Software</h2>
  <p class="abs lead">The Industry leader in Construction Software that can manage your projects from start to finish</p>
  <ul class="abs ticks">
    <li><svg width="13" height="11" viewBox="0 0 13 11"><path d="M1 6l4 4 7-9" stroke="#222" stroke-width="2" fill="none"/></svg>Lorem ipsum dolor sit amet, consectetur sed eiusmod</li>
    <li><svg width="13" height="11" viewBox="0 0 13 11"><path d="M1 6l4 4 7-9" stroke="#222" stroke-width="2" fill="none"/></svg>Lorem ipsum dolor sit amet, consectetur adipisicing</li>
    <li><svg width="13" height="11" viewBox="0 0 13 11"><path d="M1 6l4 4 7-9" stroke="#222" stroke-width="2" fill="none"/></svg>Amet, consectetur adipisicing elit, lorem ipsum dolor sit</li>
    <li><svg width="13" height="11" viewBox="0 0 13 11"><path d="M1 6l4 4 7-9" stroke="#222" stroke-width="2" fill="none"/></svg>Consectetur sed eiusmod incididunt lorem ipsum</li>
  </ul>
  <a class="abs cta sales">Contact Sales</a>
  <a class="abs cta demo">View Demo</a>

  <div class="abs thumbs">
    <div class="thumb"><div class="pic" role="img" aria-label="Excavator operator on site" style="background:linear-gradient(#d9b04a,#5d5140)"></div><p>Estimating &amp; Bidding</p></div>
    <div class="thumb"><div class="pic" role="img" aria-label="Engineers in hard hats" style="background:linear-gradient(#cfd6de,#4a4e55)"></div><p>Job Management</p></div>
    <div class="thumb"><div class="pic" role="img" aria-label="Driver in truck cab" style="background:linear-gradient(#b8c4cf,#5c6570)"></div><p>Dispatching &amp; Scheduling</p></div>
    <div class="thumb"><div class="pic" role="img" aria-label="Worker with safety gear" style="background:linear-gradient(#7fa6cf,#9a6a3c)"></div><p>Estimating &amp; Bidding</p></div>
    <div class="thumb"><div class="pic" role="img" aria-label="GPS survey tripod" style="background:linear-gradient(#5f8fc2,#c9a66e)"></div><p>GPS</p></div>
    <div class="thumb"><div class="pic" role="img" aria-label="Hand tools and hard hat" style="background:linear-gradient(#f1f1f1,#c88a3a)"></div><p>Equipment Maintenance</p></div>
    <div class="thumb"><div class="pic" role="img" aria-label="Power plant cooling towers" style="background:linear-gradient(#bcc6cf,#7f8a70)"></div><p>Fuel Tracking</p></div>
    <div class="thumb"><div class="pic" role="img" aria-label="Smartphone with gears" style="background:linear-gradient(#e6e6e6,#6d7277)"></div><p>Mobile Apps</p></div>
    <div class="thumb"><div class="pic" role="img" aria-label="Steel structure against sky" style="background:linear-gradient(#5d8cc0,#8c7a55)"></div><p>Software KeywordText</p></div>
  </div>
</section>

<svg class="abs divider" viewBox="0 0 140 24"><line x1="0" y1="12" x2="58" y2="12" stroke="#2bb04a"/><line x1="82" y1="12" x2="140" y2="12" stroke="#2bb04a"/><circle cx="70" cy="12" r="10" fill="#2bb04a"/><path d="M65 12l3.5 3.5L75 9" stroke="#fff" stroke-width="2" fill="none"/></svg>

<main>
  <article class="abs module" style="left:92px;top:818px">
    <h3>Estimating &amp; Bidding</h3>
    <div class="photo" role="img" aria-label="Excavator operator reviewing plans" style="background:linear-gradient(135deg,#e0b84a,#7d6a4c 55%,#3e3a33)"></div>
    <ul><li>Proven Process Beneit</li><li>Lorem Ipsum Proven Process</li><li>Dummy Text Proven Process</li><li>Omnis Natus Accus Process</li><li>Lorem Ipsum Process</li></ul>
    <div class="actions"><a class="btn sales green">Contact Sales</a><a class="btn more orange">Read More</a></div>
  </article>
  <article class="abs module" style="left:624px;top:818px">
    <h3>Job Management</h3>
    <div class="photo" role="img" aria-label="Team of engineers in hard hats at a plant" style="background:linear-gradient(#cfd7e0,#55595f 60%,#2d2f33)"></div>
    <ul><li>Proven Process Beneit</li><li>Lorem Ipsum Proven Process</li><li>Dummy Text Proven Process</li><li>Omnis Natus Accus Process</li><li>Lorem Ipsum Process</li></ul>
    <div class="actions"><a class="btn sales">Contact Sales</a><a class="btn more">Read More</a></div>
  </article>

  <article class="abs module" style="left:92px;top:1118px">
    <h3>Dispatching &amp; Scheduling</h3>
    <div class="photo" role="img" aria-label="Driver in a white truck cab" style="background:linear-gradient(135deg,#c7d1db,#f2f2f2 45%,#6d7680)"></div>
    <ul><li>Proven Process Beneit</li><li>Lorem Ipsum Proven Process</li><li>Dummy Text Proven Process</li><li>Omnis Natus Accus Process</li><li>Lorem Ipsum Process</li></ul>
    <div class="actions"><a class="btn sales">Contact Sales</a><a class="btn more">Read More</a></div>
  </article>
  <article class="abs module" style="left:624px;top:1118px">
    <h3>Safety Management</h3>
    <div class="photo" role="img" aria-label="Worker with hard hat and ear protection" style="background:linear-gradient(#6f9dcc,#3f5f88 50%,#8a4a2a)"></div>
    <ul><li>Proven Process Beneit</li><li>Lorem Ipsum Proven Process</li><li>Dummy Text Proven Process</li><li>Omnis Natus Accus Process</li><li>Lorem Ipsum Process</li></ul>
    <div class="actions"><a class="btn sales">Contact Sales</a><a class="btn more">Read More</a></div>
  </article>

  <article class="abs module" style="left:92px;top:1410px">
    <h3>GPS</h3>
    <div class="photo" role="img" aria-label="GPS survey instrument on tripod" style="background:linear-gradient(#3f74b0,#8db3d8 60%,#b69868)"></div>
    <ul><li>Proven Process Beneit</li><li>Lorem Ipsum Proven Process</li><li>Dummy Text Proven Process</li><li>Omnis Natus Accus Process</li><li>Lorem Ipsum Process</li></ul>
    <div class="actions"><a class="btn sales">Contact Sales</a><a class="btn more">Read More</a></div>
  </article>
  <article class="abs module" style="left:624px;top:1410px">
    <h3>Equipment Maintenance</h3>
    <div class="photo" role="img" aria-label="Hard hat, gloves and goggles on steel plate" style="background:linear-gradient(135deg,#5a4a38,#d9a13a 55%,#6b6b6b)"></div>
    <ul><li>Proven Process Beneit</li><li>Lorem Ipsum Proven Process</li><li>Dummy Text Proven Process</li><li>Omnis Natus Accus Process</li><li>Lorem Ipsum Process</li></ul>
    <div class="actions"><a class="btn sales">Contact Sales</a><a class="btn more">Read More</a></div>
  </article>

  <article class="abs module" style="left:92px;top:1692px">
    <h3>Fuel Tracking</h3>
    <div class="photo" role="img" aria-label="Power plant cooling towers" style="background:linear-gradient(#9fb4c6,#c9cfd3 50%,#6f7a5e)"></div>
    <ul><li>Proven Process Beneit</li><li>Lorem Ipsum Proven Process</li><li>Dummy Text Proven Process</li><li>Omnis Natus Accus Process</li><li>Lorem Ipsum Process</li></ul>
    <div class="actions"><a class="btn sales">Contact Sales</a><a class="btn more">Read More</a></div>
  </article>
  <article class="abs module" style="left:624px;top:1692px">
    <h3>Mobile Apps</h3>
    <div class="photo" role="img" aria-label="Smartphone with metal gears" style="background:linear-gradient(#fafafa,#b9bdc1 60%,#3a3d41)"></div>
    <ul><li>Proven Process Beneit</li><li>Lorem Ipsum Proven Process</li><li>Dummy Text Proven Process</li><li>Omnis Natus Accus Process</li><li>Lorem Ipsum Process</li></ul>
    <div class="actions"><a class="btn sales">Contact Sales</a><a class="btn more">Read More</a></div>
  </article>

  <article class="abs module" style="left:92px;top:1986px">
    <h3>Software Keyword Header</h3>
    <div class="photo" role="img" aria-label="Steel structure under construction against sky" style="background:linear-gradient(#4f82ba,#a4b8c8 50%,#7a6a48)"></div>
    <ul><li>Proven Process Beneit</li><li>Lorem Ipsum Proven Process</li><li>Dummy Text Proven Process</li><li>Omnis Natus Accus Process</li><li>Lorem Ipsum Process</li></ul>
    <div class="actions"><a class="btn sales">Contact Sales</a><a class="btn more">Read More</a></div>
  </article>
</main>

<a class="abs to-top"><svg width="10" height="16" viewBox="0 0 10 16"><path d="M5 1v14M1 5l4-4 4 4" stroke="#fff" stroke-width="2" fill="none"/></svg>BACK<br>TO TOP</a>

<footer class="abs footer" role="img" aria-label="Blurred construction site in background">
  <div class="abs tab">TRBW</div>
  <div class="abs fcol" style="left:94px">
    <h4>Softwares</h4>
    <ul><li>GroundQuote®</li><li class="current">SiteTrack®</li><li>Safety Application</li><li>The Router</li><li>GPS</li><li>FleetCare</li><li>TankLog</li><li>quotearchive.com</li><li>Mobile Apps</li><li>Mobile Apps</li></ul>
  </div>
  <div class="abs fcol" style="left:304px">
    <h4>Serices</h4>
    <ul><li>Could Services</li><li>Custom Programming</li><li>Universities</li><li>Instant Support</li></ul>
    <h4 class="second">Training &amp; Events</h4>
    <ul><li>Training Options</li><li>Dummy Links Plz Ad</li></ul>
  </div>
  <div class="abs fcol" style="left:514px">
    <h4>News</h4>
    <ul><li>Newsroom</li><li>Newsletter</li><li>Press Kit</li><li>Newsletter Subscription</li></ul>
    <h4 class="second">Careers</h4>
    <ul><li>Careers At TRBW</li><li>Careers in Construction</li></ul>
  </div>
  <div class="abs fcol" style="left:722px">
    <h4>About Us</h4>
    <ul><li>About Trbw</li><li>TRBW Culture Blog</li><li>Our Clients</li><li>Contact/More Info</li><li>The TRBW Story</li><li>Map &amp; Directions</li><li>Stability</li><li>Why Choose TRBW</li></ul>
  </div>
  <div class="abs fcol" style="left:926px">
    <h4 style="width:180px">Contact Us</h4>
    <ul class="contact-list">
      <li><span class="k">Sales :</span>800 - 555 - 0142</li>
      <li><span class="k">Support :</span>800 - 555 - 0187</li>
      <li><span class="k">Email :</span>info@trbw.com</li>
      <li><svg width="10" height="14" viewBox="0 0 10 14"><path d="M5 0a5 5 0 0 0-5 5c0 4 5 9 5 9s5-5 5-9a5 5 0 0 0-5-5zm0 7a2 2 0 1 1 0-4 2 2 0 0 1 0 4z" fill="#fff"/></svg>4820 Quarry Road,<br>Granite Falls, TX 77000</li>
    </ul>
    <h4 class="second" style="width:180px">Social Media</h4>
    <div class="social" aria-label="Social media links"><span></span><span class="on"></span><span></span><span></span><span></span></div>
    <div class="follow">Follow</div>
  </div>
</footer>

<div class="abs bottombar">
  <div class="abs copy">All Right Reserved © Copyright with www.trbw.com &nbsp;- &nbsp;2013 <span>Terms</span> <span style="margin-left:10px">Privacy Policy</span></div>
</div>

</body>
</html>
```